Heron Haulage needs Bussiness cards!

Our new trucking company needs business cards!
We need the same design with two different names and emails, everything else it's the same.
I have included our original logo so we can use it for the design.
Note: the logo to be used is the o e with the buffalo on the right side, next to the letters H and H.

Target Market(s)

Trucking, refrigerated transportation, freight

Industry/Entity Type

Business

Contact Information for Business Card

Card #1:
Marcus Whitfield
marcuswhitfield@heronhaulage.example
1-855-317-6094
(956)238-7160
4117 W. Larkin Ave.
Pharr, TX 78590
www.heronhaulage.example

Card#2:
Rosalba Quintero
rosalba@heronhaulage.example
1-855-317-6094
(956)238-7160
4117 W. Larkin Ave.
Pharr, TX 78590
www.heronhaulage.example

Font styles to use
Sans Serif

Colors
0655a3
ec1f27
ffffff

Requirements
Must have
• our logo
Nice to have
• roads on background,

```html
<!DOCTYPE html>
<html lang="en">
<head>
<meta charset="utf-8">
<title>Heron Haulage – Business Card</title>
<link href="https://fonts.googleapis.com/css2?family=Roboto+Condensed:wght@400;700;800&display=swap" rel="stylesheet">
<style>
  :root {
    --navy: #0f3163;
    --blue: #0655a3;
    --red: #ec1f27;
    --white: #ffffff;
    --ink: #6b6b6b;
    --rule: #8a8a8a;
    --page: #d9dbde;
  }
  * { box-sizing: border-box; margin: 0; padding: 0; }
  html, body {
    width: 1200px; height: 950px; overflow: hidden;
    background: var(--page);
    font-family: "Roboto Condensed", Arial, sans-serif;
  }
  .sheet {
    width: 1200px; height: 950px;
    display: flex; flex-direction: column; align-items: center; justify-content: center;
    gap: 24px;
  }
  .card {
    width: 770px; height: 440px;
    position: relative;
    box-shadow: 0 6px 18px rgba(0,0,0,.18);
  }
  /* back side */
  .card--back {
    background: var(--navy);
    display: flex; flex-direction: column; align-items: center; justify-content: center;
    color: var(--white);
  }
  .brand {
    display: flex; align-items: center; gap: 18px;
    font-weight: 800; font-size: 64px; letter-spacing: .5px; line-height: 1;
  }
  .brand__dot {
    width: 34px; height: 34px; border-radius: 50%;
    background: var(--red); flex: none;
  }
  .card--back .brand { color: var(--white); }
  .card--back .web {
    margin-top: 70px;
    font-weight: 400; font-size: 17px; letter-spacing: 4px;
  }
  /* front side */
  .card--front { background: var(--white); }
  .card--front .holder {
    position: absolute; top: 40px; right: 52px;
    font-weight: 700; font-size: 26px; color: var(--navy); letter-spacing: .5px;
    text-transform: uppercase;
  }
  .card--front .brand {
    position: absolute; top: 130px; left: 0; right: 0; justify-content: center;
    color: var(--navy); font-size: 68px;
  }
  .contact {
    position: absolute; left: 52px; right: 52px; bottom: 52px;
    border-top: 2px solid var(--rule); border-bottom: 2px solid var(--rule);
    padding: 18px 6px;
    display: flex; justify-content: space-between;
    color: var(--ink); font-size: 17px; line-height: 1.55;
  }
  .contact__col { white-space: nowrap; }
</style>
</head>
<body>
<main class="sheet">
  <section class="card card--back" aria-label="Card back">
    <div class="brand"><span class="brand__dot"></span><span>Heron Haulage</span></div>
    <p class="web">www.heronhaulage.example</p>
  </section>

  <section class="card card--front" aria-label="Card front">
    <h1 class="holder">Marcus Whitfield</h1>
    <div class="brand"><span class="brand__dot"></span><span>Heron Haulage</span></div>
    <div class="contact">
      <div class="contact__col">4117 W. Larkin Ave.<br>Pharr, TX 78590</div>
      <div class="contact__col">P : 1-855-317-6094<br>M : (956)238-7160</div>
      <div class="contact__col">marcuswhitfield@heronhaulage.example<br>www.heronhaulage.example</div>
    </div>
  </section>
</main>
</body>
</html>
```